Need Business Card for our Real Estate Business with Sales Executive's Picture

PANTONE 484 C ( RED)

PANTONE 2766 C ( BLUE

Industry/Entity Type

Real Estate

Contact Information for Business Card

Name, Mobile, email, & picture of Person
Agency Phone, address, Web address

Requirements
Must have
• Our Logo Colours, Agent Picture,

```html
<!DOCTYPE html>
<html lang="en">
<head>
<meta charset="utf-8">
<title>Dunmore Real Estate – Business Card</title>
<link href="https://fonts.googleapis.com/css2?family=Cinzel:wght@400;500&family=Tinos&family=Roboto:wght@400&display=swap" rel="stylesheet">
<style>
  :root {
    --navy: #0b1438;
    --red: #7a1420;
    --card-white: #f4f4f3;
    --backdrop: #dcdcdc;
    --text-grey: #4a4a4a;
    --photo-top: #c9ccd4;
    --photo-bottom: #1f2f6b;
  }
  * { margin: 0; padding: 0; box-sizing: border-box; }
  html, body { width: 1200px; height: 960px; overflow: hidden; }
  body { background: var(--backdrop); position: relative; font-family: "Tinos", serif; }

  .card { position: absolute; width: 600px; height: 343px; box-shadow: 1px 2px 4px rgba(0,0,0,.35); }
  .card--front { left: 314px; top: 113px; background: var(--card-white); }
  .card--back { left: 311px; top: 472px; background: var(--navy); }

  .brand { position: absolute; display: flex; align-items: center; gap: 12px; font-family: "Cinzel", serif; font-weight: 400; letter-spacing: 2px; }
  .brand__mark { width: 14px; height: 14px; background: var(--red); }
  .card--front .brand { left: 36px; top: 112px; font-size: 40px; color: var(--navy); }
  .card--back .brand { left: 0; right: 0; top: 178px; justify-content: center; font-size: 44px; color: #fff; }

  .address { position: absolute; left: 36px; top: 194px; font-size: 15px; line-height: 19px; color: var(--text-grey); }
  .contact-list { position: absolute; left: 36px; top: 241px; list-style: none; font-size: 15px; color: var(--text-grey); }
  .contact-list li { display: flex; align-items: center; gap: 8px; height: 19.5px; }
  .contact-list svg { width: 13px; height: 13px; fill: var(--navy); flex: none; }

  .agent-photo { position: absolute; left: 396px; top: 68px; width: 140px; height: 169px; border: 1.5px solid var(--navy); border-radius: 12px; background: linear-gradient(180deg, var(--photo-top) 0%, var(--photo-top) 35%, var(--photo-bottom) 100%); box-shadow: 2px 2px 3px rgba(0,0,0,.3); }
  .agent-name { position: absolute; left: 366px; width: 200px; top: 255px; text-align: center; font-family: "Cinzel", serif; font-size: 22px; color: var(--navy); }
  .agent-role { position: absolute; left: 366px; width: 200px; top: 283px; text-align: center; font-family: "Cinzel", serif; font-size: 16px; color: var(--red); }

  .web { position: absolute; left: 0; right: 0; top: 296px; text-align: center; font-family: "Roboto", sans-serif; font-size: 14px; letter-spacing: 3px; color: #fff; }
</style>
</head>
<body>
  <section class="card card--front">
    <div class="brand"><span class="brand__mark"></span>DUNMORE</div>
    <p class="address">2140 Willow Court<br>Juneau, Alaska 34512</p>
    <ul class="contact-list">
      <li><svg viewBox="0 0 16 16"><path d="M3.5 1l3 3-1.6 2c.9 2 2.3 3.4 4.1 4.2l2-1.6 3 3-2 2.4C6.5 13.5 2.3 9.3 1 3z"/></svg>614 205 7719</li>
      <li><svg viewBox="0 0 16 16"><path d="M4 0h8v16H4zM5.5 2v10h5V2zM7 13.2h2v1.3H7z" fill-rule="evenodd"/></svg>742 318 5506</li>
      <li><svg viewBox="0 0 16 16"><path d="M1 3h14v10H1zM1.5 3.5L8 9l6.5-5.5" /></svg>mark@dunmore.com</li>
      <li><svg viewBox="0 0 16 16"><path d="M8 0a8 8 0 100 16A8 8 0 008 0zm0 2c1 1.3 1.6 3.6 1.6 6S9 12.7 8 14c-1-1.3-1.6-3.6-1.6-6S7 3.3 8 2zM2.2 7h12M2.2 9h12" fill-rule="evenodd"/></svg>www.dunmore.com</li>
    </ul>
    <div class="agent-photo" role="img" aria-label="Portrait photo of the agent in a navy suit"></div>
    <p class="agent-name">MARK ELLISON</p>
    <p class="agent-role">CEO/FOUNDER</p>
  </section>

  <section class="card card--back">
    <div class="brand"><span class="brand__mark"></span>DUNMORE</div>
    <p class="web">www.dunmore.com</p>
  </section>
</body>
</html>
```